real esate business card with company logo and name

we need a business card design for a real esate company

The company name is Walsh & Brand Pty Ltd, and we have our logo designed and will upload. We want classic or moden feel. Black or white background. looks more textured. Should include folowinginformations
Owen Walsh and Lucy Brand
Sales Agents & Onsite Manager
p: 07 5948 2063
F: 07 5948 2174
M:0431 857 219
3/42 Marlow Crescent, FERNLEA QLD 4213

We want this business card looks professonal. Thank you in advance.

Industry/Entity Type

Real Estate Agent

Contact Information for Business Card

Owen Walsh and Lucy Brand
Onsite Manager & Sales Agents
p: 07 5948 2063
M:0431 857 219

Font styles to use
Serif

Colors
000000
fbfbfb
333333
959595

Requirements
Must have
• company logo and name, black or white back ground

```html
<!DOCTYPE html>
<html lang="en">
<head>
<meta charset="utf-8">
<title>Walsh &amp; Brand Pty Ltd — Business Card</title>
<link href="https://fonts.googleapis.com/css2?family=Marcellus+SC&family=Oswald:wght@400&display=swap" rel="stylesheet">
<style>
  :root {
    --ink: #000000;
    --paper: #fbfbfb;
    --charcoal: #333333;
    --grey: #959595;
    --grey-light: #c9c9c9;
    --backdrop: #e6e4e1;
  }
  * { box-sizing: border-box; margin: 0; padding: 0; }
  html, body { width: 1200px; height: 913px; overflow: hidden; }
  body {
    background: var(--backdrop);
    font-family: "Marcellus SC", Georgia, serif;
    display: flex;
    align-items: center;
    justify-content: center;
    gap: 40px;
  }
  .card {
    position: relative;
    width: 540px;
    height: 330px;
    overflow: hidden;
    box-shadow: 0 6px 18px rgba(0,0,0,.18);
  }

  /* Front */
  .card--front {
    background: radial-gradient(circle at 30% 40%, #ffffff 0%, var(--paper) 60%, #efefef 100%);
    color: var(--charcoal);
  }
  .front__watermark {
    position: absolute;
    left: 40px; top: 80px;
    width: 230px; height: 230px;
    background: var(--grey);
    opacity: .12;
  }
  .brand {
    position: absolute;
    right: 34px; top: 30px;
    display: flex;
    align-items: center;
    gap: 10px;
  }
  .brand__mark { width: 16px; height: 16px; background: var(--grey); }
  .brand__name { font-size: 17px; color: var(--grey); letter-spacing: 1px; }
  .agents {
    position: absolute;
    right: 34px; top: 92px;
    text-align: right;
  }
  .agents__names { font-size: 23px; color: var(--ink); letter-spacing: .5px; }
  .agents__rule { height: 1px; background: var(--charcoal); width: 300px; margin: 6px 0 5px auto; }
  .agents__role { font-size: 14px; color: var(--grey); letter-spacing: 1px; }
  .address {
    position: absolute;
    right: 34px; top: 190px;
    text-align: right;
    font-size: 15px;
    line-height: 1.45;
    color: var(--ink);
  }
  .contact {
    position: absolute;
    left: 30px; bottom: 28px;
    width: 200px;
    border-top: 1px solid var(--charcoal);
    padding-top: 8px;
    list-style: none;
  }
  .contact__item {
    display: flex;
    align-items: center;
    gap: 8px;
    font-size: 14px;
    color: var(--ink);
    line-height: 1.45;
  }
  .contact__icon { width: 11px; height: 11px; fill: var(--charcoal); }

  /* Back */
  .card--back {
    background: radial-gradient(circle at 60% 30%, #262626 0%, #111111 55%, var(--ink) 100%);
    display: flex;
    flex-direction: column;
    align-items: center;
    justify-content: center;
    gap: 20px;
  }
  .back__mark { width: 60px; height: 60px; background: var(--grey-light); }
  .back__name {
    font-family: "Oswald", "Arial Narrow", sans-serif;
    font-size: 26px;
    letter-spacing: 2px;
    color: var(--grey-light);
    text-transform: uppercase;
  }
</style>
</head>
<body>
  <section class="card card--front" aria-label="Card front">
    <div class="front__watermark" aria-hidden="true"></div>
    <div class="brand">
      <span class="brand__mark" aria-hidden="true"></span>
      <span class="brand__name">Walsh &amp; Brand Pty Ltd</span>
    </div>
    <div class="agents">
      <p class="agents__names">Owen Walsh &amp; Lucy Brand</p>
      <div class="agents__rule"></div>
      <p class="agents__role">Sales Agents &amp; Onsite Manager</p>
    </div>
    <address class="address">
      3/42 Marlow Crescent<br>
      FERNLEA QLD 4213
    </address>
    <ul class="contact">
      <li class="contact__item">
        <svg class="contact__icon" viewBox="0 0 12 12" aria-label="Phone"><path d="M2.5 0.8l2 2-1 1.4c.6 1.5 1.8 2.7 3.3 3.3l1.4-1 2 2-1.2 1.6C5.5 10 1.9 6.4 1 2z"/></svg>
        07 5948 2063
      </li>
      <li class="contact__item">
        <svg class="contact__icon" viewBox="0 0 12 12" aria-label="Fax"><rect x="3" y="0.5" width="6" height="4"/><rect x="0.5" y="5" width="11" height="6" rx="1"/></svg>
        07 5948 2174
      </li>
      <li class="contact__item">
        <svg class="contact__icon" viewBox="0 0 12 12" aria-label="Mobile"><path d="M3 0.5h6v11H3z M4 1.5v7.5h4V1.5z"/></svg>
        0431 857 219
      </li>
    </ul>
  </section>

  <section class="card card--back" aria-label="Card back">
    <span class="back__mark" aria-hidden="true"></span>
    <p class="back__name">Walsh &amp; Brand Pty Ltd.</p>
  </section>
</body>
</html>
```